Wordpress Design (uncoded) Auction & Real Estate 3 in 1

This will be an uncoded Wordpress theme design only. Winning designer will provide PSD source files.

We need a wordpress themedesign for an established auction and real estate company based in Pennsylvania. The client wants one overall theme for their primary company website with 2 child themes, one for auction division and one for real estate division. Each child theme will have it's own color scheme and some variation in layout.

The primary company logo is Blue with white/black/silver elements. (see attached zip file)

The auction division logo is Gold with black/white elements (see attached zip file)

The real estate division logo is Green with white/black/silver elements. (see attached zip file)

Also attached are 2 PDF files showing a sample layout that the client came up with that they really like; however, this should only be used as a starting point. We want to see what creative, clean layouts you can come up with.

Industry/Entity Type

Real Estate

Requirements
Must have
• - We will require winning designer to provide a layered PSD (Adobe photoshop) concept files, along with any non-standard font files used.

A slideshow element on the home page using the placeholder image provided.

Primary Site navigation for merrowtonhalvecompanies.example:

Home
Services
-Auctions/Appraisals
-Real Estate Auctions
-Real Estate Listings
About Us
-History
-Auction Center
Contact Us

Secondary site - halvegavelhouse.example navigation:
Home
Auctions
Buy/Sell
Collections
Services
Contact Us

Secondary site - merrowtonhalve.example
Home
Properties
Real Estate Auctions
Buying
Selling
Area Info
About Us
Contact Us
Nice to have
• Sidebar widgets: Email sign-up form - Featured Auctions - Featured Assets for Sale

```html
<!DOCTYPE html>
<html lang="en">
<head>
<meta charset="utf-8">
<title>Merrowton Halve Real Estate</title>
<link rel="stylesheet" href="https://fonts.googleapis.com/css2?family=Arimo:wght@400;700&family=Marcellus&display=swap">
<style>
:root{
  --green:#2f7a4c;
  --green-dark:#1f5a36;
  --green-light:#3f9460;
  --bg:#e2e2e2;
  --panel:#ffffff;
  --dark:#2b2b2b;
  --footer:#3b3535;
  --footer-base:#2a2626;
  --text:#222;
  --muted:#6b5a40;
  --field-border:#444;
}
*{box-sizing:border-box;margin:0;padding:0}
html,body{width:1115px;height:1200px;overflow:hidden}
body{position:relative;background:linear-gradient(180deg,#d6d6d6 0,#ececec 120px,var(--bg) 600px,#dcdcdc 1066px);font-family:"Arimo",Arial,sans-serif;color:var(--text)}
.abs{position:absolute}
.top-rule{left:0;top:0;width:1115px;height:3px;background:#5a5252}

.brand{left:121px;top:32px;display:flex;align-items:center;gap:10px;color:var(--green-dark);font-family:"Arimo",Arial,sans-serif;font-weight:700}
.brand-dot{width:70px;height:70px;border-radius:50%;background:var(--green)}
.brand-name{line-height:1.05}
.brand-name .l1{font-size:28px;display:block;letter-spacing:.5px}
.brand-name .l2{font-size:19px;display:block;letter-spacing:3px}
.brand-name .l3{font-size:10px;display:block;letter-spacing:1px;margin-top:3px}

.search{left:800px;top:50px;width:205px;height:30px;background:#fff;border:1px solid #c8c8c8;display:flex;align-items:center;justify-content:space-between;padding:0 8px;font-size:13px;color:#9a9a9a}

.nav{left:123px;top:134px;width:880px;height:43px;border-radius:5px;background:linear-gradient(180deg,var(--green-light),var(--green) 55%,var(--green-dark));box-shadow:0 1px 2px rgba(0,0,0,.3)}
.nav-tab{left:137px;top:140px;width:74px;height:44px;background:linear-gradient(180deg,#3a3a3a,#2b2b2b 70%,#555);border-radius:4px 4px 0 0}
.nav-item{top:149px;color:#fff;font-size:13.5px;letter-spacing:.2px}
.nav-sep{top:142px;width:1px;height:27px;background:rgba(255,255,255,.3)}

.hero{left:121px;top:191px;width:883px;height:336px;background:var(--panel);box-shadow:0 6px 8px -6px rgba(0,0,0,.25)}
.hero-photo{left:128px;top:201px;width:614px;height:318px;background:linear-gradient(180deg,#e6d3b3 0,#c8b08a 35%,#6a4a3a 65%,#2a2220 100%)}
.signup{left:743px;top:201px;width:248px;height:318px;background:linear-gradient(180deg,#3a3a3a,#1f1f1f)}
.ribbon{background:linear-gradient(180deg,var(--green-light),var(--green) 60%,var(--green-dark));color:#fff;font-family:"Marcellus",serif}
.signup-title{left:754px;top:213px;width:244px;height:43px;font-size:19px;padding:9px 0 0 13px;border-radius:4px 0 0 0}
.fold{left:991px;top:256px;width:0;height:0;border-top:7px solid #123a22;border-right:7px solid transparent}
.field{left:760px;width:214px;height:31px;background:#fff;border:1px solid var(--field-border);font-size:12.5px;color:#666;padding:7px 7px}
.signup-btn{left:759px;top:447px;width:118px;height:36px;border-radius:6px;font-size:16px;display:flex;align-items:center;gap:8px;padding-left:13px}

.main{left:122px;top:557px;width:877px;height:474px;background:var(--panel)}
.vdots{width:0;border-left:1px dotted #bdbdbd}
.section-title{height:33px;border-radius:0 6px 6px 0;font-size:18px;padding:6px 0 0 10px}

.thumb{width:100px;height:75px;border:1px solid #ccc;padding:2px;background:#fff}
.thumb i{display:block;width:100%;height:100%;background:linear-gradient(180deg,#cfe0f0 0,#e8eef2 35%,#6d8a5a 60%,#4f7a3a 100%)}
.listing-kicker{font-size:13.5px;font-weight:700;color:var(--muted);letter-spacing:.8px}
.listing-meta{font-size:12px;line-height:18px}
.listing-meta b{margin-right:4px}
.listing-body{width:455px;font-size:11.5px;line-height:16.7px;text-align:justify}
.btn{width:102px;height:28px;border-radius:5px;color:#fff;font-weight:700;font-size:13px;display:flex;align-items:center;gap:8px;padding-left:11px}
.btn-green{background:linear-gradient(180deg,var(--green-light),var(--green-dark))}
.btn-dark{background:linear-gradient(180deg,#555,#1f1f1f)}
.hrule{height:0;border-top:1px dotted #bdbdbd}

.side-link{font-family:"Marcellus",serif;font-size:12.5px;color:var(--green-dark);text-decoration:underline;letter-spacing:.8px}
.side-photo{border:1px solid #ccc;padding:3px;background:#fff}
.side-photo i{display:block;width:100%;height:100%}
.side-text{font-size:11.5px;line-height:14px;width:210px}
.read-more{width:67px;height:18px;border-radius:4px;background:#1c1212;color:#fff;font-size:11.5px;font-style:italic;font-weight:700;text-align:center;line-height:18px}

.footer-strip{left:0;top:1066px;width:1115px;height:6px;background:var(--green)}
.footer{left:0;top:1072px;width:1115px;height:106px;background:var(--footer)}
.footer-base{left:0;top:1178px;width:1115px;height:22px;background:var(--footer-base)}
.footer-mark{left:181px;top:1087px;width:63px;height:63px;border-radius:50%;border:2px solid #ddd}
.f-head{top:1093px;color:#fff;font-size:13.5px}
.f-item{color:#e6e6e6;font-size:12px}
.f-item::before{content:"» ";font-size:10px}
.f-base{top:1182px;color:#d8d8d8;font-size:12px}
</style>
</head>
<body>
<div class="abs top-rule"></div>

<header>
  <div class="abs brand">
    <span class="brand-dot"></span>
    <span class="brand-name"><span class="l1">MERROWTON HALVE</span><span class="l2">REAL ESTATE</span><span class="l3">A MERROWTON HALVE COMPANY</span></span>
  </div>
  <div class="abs search"><span>search</span>
    <svg width="16" height="16" viewBox="0 0 16 16"><circle cx="6.5" cy="6.5" r="4.5" fill="none" stroke="#6a9a6a" stroke-width="2.5"/><line x1="10" y1="10" x2="14" y2="14" stroke="#6a9a6a" stroke-width="3"/></svg>
  </div>
</header>

<nav>
  <div class="abs nav"></div>
  <div class="abs nav-tab"></div>
  <span class="abs nav-item" style="left:155px">HOME</span>
  <span class="abs nav-sep" style="left:233px"></span>
  <span class="abs nav-item" style="left:254px">ABOUT US</span>
  <span class="abs nav-sep" style="left:347px"></span>
  <span class="abs nav-item" style="left:378px">HISTORY</span>
  <span class="abs nav-item" style="left:494px">AUCTION CENTER</span>
  <span class="abs nav-item" style="left:666px">CONTACT US</span>
</nav>

<section>
  <div class="abs hero"></div>
  <div class="abs hero-photo" role="img" aria-label="Slideshow photo: auctioneers presenting a framed painting to a seated audience in an auction hall"></div>
  <div class="abs signup"></div>
  <div class="abs ribbon signup-title">EMAIL SIGN-UP FORM</div>
  <div class="abs fold"></div>
  <div class="abs field" style="top:287px">First Name</div>
  <div class="abs field" style="top:338px">Last Name</div>
  <div class="abs field" style="top:392px">Email Address</div>
  <div class="abs ribbon signup-btn">SIGN UP
    <svg width="20" height="18" viewBox="0 0 20 18"><path d="M2 2h9v4M11 12v4H2V2" fill="none" stroke="#ddd" stroke-width="2"/><path d="M8 9h9M13 5l4 4-4 4" fill="none" stroke="#ddd" stroke-width="2"/></svg>
  </div>
</section>

<main>
  <div class="abs main"></div>
  <div class="abs vdots" style="left:139px;top:613px;height:405px"></div>
  <div class="abs vdots" style="left:743px;top:613px;height:405px"></div>

  <div class="abs ribbon section-title" style="left:139px;top:572px;width:438px">Shop Equipment/tools * Pork Processing Items</div>

  <article>
    <div class="abs thumb" style="left:152px;top:621px"><i role="img" aria-label="Photo of an auction crowd on the lawn before a white house"></i></div>
    <div class="abs listing-kicker" style="left:264px;top:625px">LIVE ON-SITE AUCTION</div>
    <div class="abs listing-meta" style="left:264px;top:644px"><b>Begins:</b> Saturday, March 16, 2013 at 10:00 AM EDT<br><b>Location:</b> 2280 Kestrel Lane Dunmoor, KY 40999</div>
    <p class="abs listing-body" style="left:263px;top:696px">Corvane BS3F High Lift, simply dummy text of the printing and typesetting industry simply dummy text of the printing and typesetting industry 600 Series Harlow tractor w/Thornbeck Loader, Dune buggy, 1207 KT Cutditioner: SHOP &amp; MISCELLANIOUS &amp; PORK PROCESSING ITEMS.</p>
    <div class="abs btn btn-green" style="left:152px;top:709px"><svg width="24" height="12" viewBox="0 0 24 12"><rect x="0" y="1" width="10" height="10" rx="2" fill="#fff"/><path d="M13 2h10M13 6h10M13 10h10" stroke="#fff" stroke-width="2"/></svg>Details</div>
    <div class="abs btn btn-dark" style="left:152px;top:745px"><svg width="20" height="16" viewBox="0 0 20 16"><rect x="1" y="3" width="13" height="12" rx="1" fill="none" stroke="#fff" stroke-width="1.5"/><rect x="6" y="1" width="13" height="11" rx="1" fill="#fff"/></svg>Photos</div>
  </article>
  <div class="abs hrule" style="left:150px;top:788px;width:581px"></div>
  <article>
    <div class="abs thumb" style="left:152px;top:806px"><i role="img" aria-label="Photo of an auction crowd on the lawn before a white house"></i></div>
    <div class="abs listing-kicker" style="left:264px;top:810px">LIVE ON-SITE AUCTION</div>
    <div class="abs listing-meta" style="left:264px;top:829px"><b>Begins:</b> Saturday, March 16, 2013 at 10:00 AM EDT<br><b>Location:</b> 2280 Kestrel Lane Dunmoor, KY 40999</div>
    <p class="abs listing-body" style="left:263px;top:881px">Corvane BS3F High Lift, simply dummy text of the printing and typesetting industry simply dummy text of the printing and typesetting industry 600 Series Harlow tractor w/Thornbeck Loader, Dune buggy, 1207 KT Cutditioner: SHOP &amp; MISCELLANIOUS &amp; PORK PROCESSING ITEMS.</p>
    <div class="abs btn btn-green" style="left:152px;top:894px"><svg width="24" height="12" viewBox="0 0 24 12"><rect x="0" y="1" width="10" height="10" rx="2" fill="#fff"/><path d="M13 2h10M13 6h10M13 10h10" stroke="#fff" stroke-width="2"/></svg>Details</div>
    <div class="abs btn btn-dark" style="left:152px;top:930px"><svg width="20" height="16" viewBox="0 0 20 16"><rect x="1" y="3" width="13" height="12" rx="1" fill="none" stroke="#fff" stroke-width="1.5"/><rect x="6" y="1" width="13" height="11" rx="1" fill="#fff"/></svg>Photos</div>
  </article>

  <aside>
    <div class="abs ribbon section-title" style="left:743px;top:572px;width:215px;font-size:20px;padding-left:24px">Featured Auctions</div>
    <div class="abs side-link" style="left:756px;top:613px">TRACTOR * HI LIFT * MACHINERY</div>
    <div class="abs side-photo" style="left:765px;top:637px;width:148px;height:72px"><i role="img" aria-label="Photo of a villa with palm trees and a lawn" style="background:linear-gradient(180deg,#c9d8e6 0,#d8c8b4 45%,#5f8a45 75%,#487a30 100%)"></i></div>
    <p class="abs side-text" style="left:757px;top:719px"><b>Saturday</b> March 16, 2013 at 10:00 AM</p>
    <p class="abs side-text" style="left:757px;top:736px">simply dummy text of the printing and typesetting industry.</p>
    <div class="abs read-more" style="left:757px;top:775px">read more</div>

    <div class="abs ribbon section-title" style="left:743px;top:820px;width:231px;font-size:20px;padding-left:13px">Featured Assets for Sale</div>
    <div class="abs side-photo" style="left:759px;top:867px;width:195px;height:82px"><i role="img" aria-label="Photo of auctioneers in suits calling bids at an outdoor sale" style="background:linear-gradient(180deg,#8a6a5a 0,#c9c2b6 40%,#3a3a3e 70%,#5a7a3a 100%)"></i></div>
    <p class="abs side-text" style="left:759px;top:957px;width:220px">simply dummy text of the printing and type setting industry dummy text of the printing and type.</p>
    <div class="abs read-more" style="left:757px;top:1006px">read more</div>
  </aside>
</main>

<footer>
  <div class="abs footer-strip"></div>
  <div class="abs footer"></div>
  <div class="abs footer-base"></div>
  <div class="abs footer-mark"></div>
  <span class="abs f-head" style="left:320px">HOME</span>
  <span class="abs f-head" style="left:419px">SERVICES</span>
  <span class="abs f-item" style="left:419px;top:1116px">Auction</span>
  <span class="abs f-item" style="left:419px;top:1135px">Real Estate</span>
  <span class="abs f-item" style="left:419px;top:1153px">LANDWAVE</span>
  <span class="abs f-head" style="left:543px">ABOUT US</span>
  <span class="abs f-item" style="left:543px;top:1116px">History</span>
  <span class="abs f-item" style="left:543px;top:1135px">Auction Center</span>
  <span class="abs f-head" style="left:670px">CONTACT US</span>
  <span class="abs f-item" style="left:670px;top:1116px">Privacy</span>
  <span class="abs f-base" style="left:173px">555 010 4821</span>
  <span class="abs f-base" style="left:284px">88 Quarry Mill Road , Ashvale, PA 19999</span>
  <span class="abs f-base" style="right:111px">(C) 2013 The Merrowton Halve Companies</span>
</footer>
</body>
</html>
```